Business Card Design Project

I require a business card with the following information on them for various different people;
name
m:
f:
e:
I have a logo already and will attached that. We are in the construction industry. I require something clean and simple but eye catching at the same time. You can use another colour with our logo if you like and you can style the logo as well if you wish. I am open.
Also it needs to be front and back design.
Industry/Entity Type
Construction
Requirements
Must have
- Logo, name, mobile, fax and email address.
Front and back design

```html
<!DOCTYPE html>
<html lang="en">
<head>
<meta charset="utf-8">
<title>Northfield Builders – Business Cards</title>
<link rel="stylesheet" href="https://fonts.googleapis.com/css2?family=PT+Sans:wght@400;700&display=swap">
<style>
  :root {
    --backdrop: #ecebe8;
    --card-white: #ffffff;
    --slate: #343844;
    --slate-light: #4a4f5c;
    --green: #3d7a22;
    --green-mid: #5c9e2e;
    --green-light: #b9d65a;
    --silver: #c9cacd;
    --ink: #5d5d5d;
    --ink-soft: #7a7a7a;
  }
  * { box-sizing: border-box; margin: 0; padding: 0; }
  html, body { width: 1200px; height: 1169px; overflow: hidden; }
  body {
    background: var(--backdrop);
    font-family: "PT Sans", sans-serif;
    position: relative;
  }
  .card {
    position: absolute;
    width: 525px;
    height: 300px;
    overflow: hidden;
    box-shadow: 0 1px 3px rgba(0,0,0,0.25);
  }
  .front { left: 36px; background: var(--card-white); }
  .back  { left: 642px; background: var(--slate); }
  .row-1 { top: 45px; }
  .row-2 { top: 427px; }
  .row-3 { top: 828px; }

  .wave { position: absolute; inset: 0; width: 525px; height: 300px; }

  .brand {
    position: absolute;
    left: 38px;
    top: 38px;
    display: flex;
    align-items: center;
    gap: 12px;
    font-weight: 400;
    font-size: 34px;
    letter-spacing: 0.5px;
    color: var(--green-mid);
    line-height: 1;
  }
  .brand-mark {
    width: 30px; height: 30px;
    background: var(--green-mid);
  }

  .holder {
    position: absolute;
    left: 37px;
    top: 194px;
    font-size: 17px;
    font-weight: 700;
    color: var(--ink);
  }
  .holder .title { font-weight: 400; font-size: 13px; color: var(--ink-soft); }

  .contact {
    position: absolute;
    right: 26px;
    top: 216px;
    list-style: none;
    color: #fff;
    font-size: 13px;
    text-align: right;
  }
  .contact li { height: 21.5px; display: flex; justify-content: flex-end; align-items: center; gap: 10px; }
  .contact svg { width: 10px; height: 10px; fill: #fff; }

  .back-name {
    position: absolute;
    inset: 0;
    display: flex;
    align-items: center;
    justify-content: center;
    font-size: 50px;
    font-weight: 400;
    letter-spacing: 1px;
    color: #fff;
  }
  .back.glow { background: radial-gradient(ellipse 180px 160px at 48% 38%, #f4f5f2 0%, #a9abb0 35%, var(--slate-light) 70%, var(--slate) 100%); }
  .back.glow-wide { background: radial-gradient(ellipse 240px 220px at 45% 40%, #f7f8f5 0%, #c9cacd 40%, #6a6e78 75%, var(--slate) 100%); }
  .back.glow-wide .back-name { color: var(--slate); }
</style>
</head>
<body>

<svg width="0" height="0" style="position:absolute" aria-hidden="true">
  <defs>
    <linearGradient id="greenSweep" x1="0" y1="0" x2="1" y2="0">
      <stop offset="0" stop-color="#4f8f23"/>
      <stop offset="0.35" stop-color="#a9cc55"/>
      <stop offset="0.7" stop-color="#4a8a25"/>
      <stop offset="1" stop-color="#3a7420"/>
    </linearGradient>
    <linearGradient id="silverSweep" x1="0" y1="0" x2="1" y2="0">
      <stop offset="0" stop-color="#8f9096"/>
      <stop offset="0.4" stop-color="#ffffff"/>
      <stop offset="1" stop-color="#a0a1a6"/>
    </linearGradient>
    <linearGradient id="slateSweep" x1="0" y1="0" x2="1" y2="0">
      <stop offset="0" stop-color="#6d707a"/>
      <stop offset="0.35" stop-color="#e6e7e9"/>
      <stop offset="0.7" stop-color="#5a5e69"/>
      <stop offset="1" stop-color="#343844"/>
    </linearGradient>
    <linearGradient id="limeSweep" x1="0" y1="0" x2="1" y2="0">
      <stop offset="0" stop-color="#4f9a2a"/>
      <stop offset="0.4" stop-color="#c6df6a"/>
      <stop offset="1" stop-color="#8fc042"/>
    </linearGradient>
    <symbol id="icon-phone" viewBox="0 0 10 10"><path d="M2 0.5l1.6 2-1 1c.6 1.3 1.6 2.3 2.9 2.9l1-1 2 1.6-1 1.8C4 8.6 1.4 6 0.2 1.5z"/></symbol>
    <symbol id="icon-fax" viewBox="0 0 10 10"><rect x="2.5" y="0.5" width="5" height="3"/><rect x="0.5" y="4" width="9" height="5" rx="1"/></symbol>
    <symbol id="icon-mail" viewBox="0 0 10 10"><path d="M0.5 2h9v6h-9z M0.5 2l4.5 3.5 4.5-3.5" stroke="#343844" stroke-width="0.6"/></symbol>
  </defs>
</svg>

<!-- Row 1 -->
<section class="card front row-1">
  <svg class="wave" viewBox="0 0 525 300" aria-hidden="true">
    <path d="M0 220 C110 270 210 255 290 180 C360 118 440 100 525 97 L525 120 C440 124 370 140 300 195 C220 258 110 280 0 240 Z" fill="url(#silverSweep)"/>
    <path d="M0 248 C120 290 230 270 305 205 C375 145 445 126 525 124 L525 300 L0 300 Z" fill="url(#greenSweep)"/>
    <path d="M28 278 C150 300 250 262 320 200 C380 150 440 134 500 130" fill="none" stroke="#fff" stroke-width="1.5"/>
  </svg>
  <div class="brand"><span class="brand-mark"></span>Northfield Builders</div>
  <p class="holder">Your Name <span class="title">/ Title</span></p>
  <ul class="contact">
    <li>123-456-7890 <svg><use href="#icon-phone"/></svg></li>
    <li>123-456-7890 <svg><use href="#icon-fax"/></svg></li>
    <li>name@website.com <svg><use href="#icon-mail"/></svg></li>
  </ul>
</section>
<section class="card back row-1 glow"><p class="back-name">Northfield Builders</p></section>

<!-- Row 2 -->
<section class="card front row-2">
  <svg class="wave" viewBox="0 0 525 300" aria-hidden="true">
    <path d="M0 220 C110 260 210 240 290 175 C360 118 440 98 525 94 L525 116 C440 120 370 138 300 190 C220 250 110 270 0 240 Z" fill="url(#limeSweep)"/>
    <path d="M0 250 C120 285 230 265 305 200 C375 142 445 122 525 120 L525 300 L0 300 Z" fill="url(#slateSweep)"/>
    <path d="M28 280 C150 300 250 262 320 198 C380 148 440 130 500 127" fill="none" stroke="#fff" stroke-width="1.5"/>
  </svg>
  <div class="brand"><span class="brand-mark"></span>Northfield Builders</div>
  <p class="holder">Your Name <span class="title">/ Title</span></p>
  <ul class="contact">
    <li>123-456-7890 <svg><use href="#icon-phone"/></svg></li>
    <li>123-456-7890 <svg><use href="#icon-fax"/></svg></li>
    <li>name@website.com <svg><use href="#icon-mail"/></svg></li>
  </ul>
</section>
<section class="card back row-2 glow-wide"><p class="back-name">Northfield Builders</p></section>

<!-- Row 3 -->
<section class="card front row-3">
  <svg class="wave" viewBox="0 0 525 300" aria-hidden="true">
    <path d="M0 225 C110 262 210 240 290 172 C360 115 440 96 525 93 L525 116 C440 120 370 138 300 190 C220 252 110 272 0 245 Z" fill="url(#limeSweep)"/>
    <path d="M0 252 C120 286 230 264 305 198 C375 140 445 121 525 119 L525 300 L0 300 Z" fill="#343844"/>
    <path d="M28 282 C150 300 250 262 320 198 C380 148 440 130 500 127" fill="none" stroke="#fff" stroke-width="1.5"/>
  </svg>
  <div class="brand"><span class="brand-mark"></span>Northfield Builders</div>
  <p class="holder">Your Name <span class="title">/ Title</span></p>
  <ul class="contact">
    <li>123-456-7890 <svg><use href="#icon-phone"/></svg></li>
    <li>123-456-7890 <svg><use href="#icon-fax"/></svg></li>
    <li>name@website.com <svg><use href="#icon-mail"/></svg></li>
  </ul>
</section>
<section class="card back row-3"><p class="back-name">Northfield Builders</p></section>

</body>
</html>
```